Need Business Card for our Real Estate Business with Sales Executive's Picture

PANTONE 484 C ( RED)

PANTONE 2766 C ( BLUE

Industry/Entity Type

Real Estate

Contact Information for Business Card

Name, Mobile, email, & picture of Person
Agency Phone, address, Web address

Requirements
Must have
• Our Logo Colours, Agent Picture,

```html
<!DOCTYPE html>
<html lang="en">
<head>
<meta charset="utf-8">
<title>Meridian Real Estate – Business Card</title>
<link href="https://fonts.googleapis.com/css2?family=Open+Sans:wght@400;600;700&display=swap" rel="stylesheet">
<style>
  :root {
    --navy: #16295e;
    --red: #a5302a;
    --white: #ffffff;
    --paper: #f7f7f8;
    --backdrop: #dcdcdc;
    --ink: #1e2f63;
  }
  * { box-sizing: border-box; margin: 0; padding: 0; }
  html, body { width: 1200px; height: 852px; overflow: hidden; }
  body {
    background: var(--backdrop);
    font-family: "Open Sans", Arial, sans-serif;
    position: relative;
  }
  .card {
    position: absolute;
    width: 525px;
    height: 300px;
    border-radius: 18px;
    overflow: hidden;
    top: 276px;
  }
  /* back of card */
  .card-back { left: 45px; background: var(--navy); color: var(--white); }
  .brand {
    position: absolute; left: 0; right: 0; top: 108px;
    display: flex; justify-content: center; align-items: center; gap: 12px;
  }
  .brand-mark { width: 14px; height: 14px; background: var(--red); }
  .brand-name {
    font-weight: 600; font-size: 34px; letter-spacing: 5px; text-transform: uppercase;
  }
  .brand-rule {
    position: absolute; left: 150px; right: 150px; top: 166px; height: 1px; background: var(--white);
  }
  .back-web {
    position: absolute; left: 0; right: 0; top: 236px; text-align: center;
    font-size: 13px; letter-spacing: .3px;
  }
  .accent-line { position: absolute; top: 246px; height: 3px; width: 70px; background: var(--red); }
  .accent-line.left { left: 70px; transform: rotate(-8deg); }
  .accent-line.right { right: 70px; transform: rotate(-8deg); }

  /* front of card */
  .card-front { left: 630px; background: var(--paper); }
  .card-front svg.shapes { position: absolute; inset: 0; }
  .agent-name {
    position: absolute; left: 22px; top: 123px; color: var(--white);
    font-weight: 700; font-size: 16px;
  }
  .agent-title {
    position: absolute; left: 22px; top: 142px; color: var(--white);
    font-size: 10px;
  }
  .contact {
    position: absolute; left: 22px; top: 178px; color: var(--ink);
    font-size: 11.5px; line-height: 17px; list-style: none;
  }
  .contact li { display: flex; align-items: center; gap: 8px; }
  .contact .icon {
    width: 11px; height: 11px; border-radius: 50%; background: var(--red); flex: none;
  }
  .contact .address { padding-left: 0; margin-bottom: 3px; }
  .contact .web span { color: var(--red); }
</style>
</head>
<body>

  <section class="card card-back" aria-label="Card back">
    <div class="brand">
      <span class="brand-mark"></span>
      <span class="brand-name">Meridian Real Estate</span>
    </div>
    <div class="brand-rule"></div>
    <span class="accent-line left"></span>
    <p class="back-web">www.meridianrealty.com</p>
    <span class="accent-line right"></span>
  </section>

  <section class="card card-front" aria-label="Card front">
    <svg class="shapes" width="525" height="300" viewBox="0 0 525 300">
      <defs>
        <linearGradient id="portraitTone" x1="0" y1="0" x2="1" y2="1">
          <stop offset="0" stop-color="#f2eeea"/>
          <stop offset=".55" stop-color="#8a6a55"/>
          <stop offset="1" stop-color="#1f3a82"/>
        </linearGradient>
      </defs>
      <polygon points="150,88 330,88 330,118 125,118" fill="var(--navy)"/>
      <rect x="300" y="0" width="225" height="258" fill="url(#portraitTone)" role="img" aria-label="Portrait photo of the sales executive in a navy suit"/>
      <polygon points="0,116 252,116 214,162 0,162" fill="var(--red)"/>
      <polygon points="0,284 340,284 372,258 525,258 525,300 0,300" fill="var(--navy)"/>
      <polygon points="440,258 525,232 525,258" fill="var(--red)"/>
    </svg>

    <p class="agent-name">Laura Bennett</p>
    <p class="agent-title">Managing Director</p>

    <ul class="contact">
      <li class="address">410 Harbor Lane #2210,<br>Brookfield, CO 80521</li>
      <li><span class="icon"></span>555.201.4478</li>
      <li><span class="icon"></span>555-308-6612</li>
      <li><span class="icon"></span>lbennett@meridianrealty.com</li>
      <li class="web"><span class="icon"></span>www.<span>meridianrealty</span>.com</li>
    </ul>
  </section>

</body>
</html>
```